Business card for my new company (Accounting firm)

I need a business card for my new business Brightwell Advisory and Ledger SA. Our services are accounting, tax, audit and financial management. Our customers are small companies, start-ups and new companies. The final design has to show financial security, trust and growth. Please find our logo attached to the business card. Text for the business card: Brightwell Advisory and Ledger SA Tomas Varenholt Director and Founder Certified Accountant Tel. 022 418 57 34 tv@clairevalconseil.ch www.clairevalconseil.ch Rue des Vergières 27 1201 Geneva
Target Market(s)
Our customers are small companies, start-ups and new companies.
Industry/Entity Type
Finance And Accounting
Contact Information for Business Card
Claireval Conseil et Comptes SA
Tomas Varenholt
Directeur et Fondateur
Expert-comptable diplômé
Tél. 022 418 57 34
tv@clairevalconseil.ch
www.clairevalconseil.ch
Rue des Vergières 27
1201 Genève

```html
<!DOCTYPE html>
<html lang="fr">
<head>
<meta charset="utf-8">
<title>Claireval Conseil et Comptes SA – Carte de visite</title>
<link rel="stylesheet" href="https://fonts.googleapis.com/css2?family=Roboto:wght@300;400;500&display=swap">
<style>
  :root {
    --backdrop: #242222;
    --navy: #1b6392;
    --sky: #31b0e0;
    --sky-pattern: #4bbbe5;
    --paper: #ffffff;
    --ink: #3d3d3d;
  }
  * { box-sizing: border-box; margin: 0; padding: 0; }
  html, body {
    width: 1125px;
    height: 1200px;
    overflow: hidden;
    background: var(--backdrop);
    font-family: "Roboto", Arial, sans-serif;
  }
  .canvas { position: relative; width: 1125px; height: 1200px; }
  .card {
    position: absolute;
    left: 171px;
    width: 826px;
    height: 471px;
    overflow: hidden;
    box-shadow: 0 3px 8px rgba(0,0,0,0.55);
  }
  .card--front { top: 106px; background: var(--navy); }
  .card--back { top: 639px; background: var(--sky); }

  .front-peak { position: absolute; inset: 0; width: 100%; height: 100%; }

  .contact {
    position: absolute;
    left: 44px;
    top: 48px;
    color: var(--paper);
    font-weight: 300;
  }
  .contact__name { font-size: 31px; font-weight: 500; line-height: 1.1; }
  .contact__role { font-size: 21px; line-height: 26px; }
  .contact__address { margin-top: 13px; font-size: 20px; line-height: 25px; }
  .contact__list { list-style: none; margin-top: 13px; }
  .contact__list li {
    display: flex;
    align-items: center;
    gap: 9px;
    font-size: 20px;
    line-height: 26px;
  }
  .contact__list svg { width: 19px; height: 19px; fill: var(--paper); flex: none; }

  .brand-name {
    position: absolute;
    left: 391px;
    top: 330px;
    width: 300px;
    text-align: center;
    color: var(--ink);
    font-size: 34px;
    font-weight: 400;
    line-height: 40px;
    letter-spacing: 1px;
  }

  .back-pattern {
    position: absolute;
    inset: 0;
    background: linear-gradient(135deg, var(--sky) 0%, var(--sky-pattern) 50%, var(--sky) 100%);
  }
  .back-brand {
    position: absolute;
    right: 60px;
    bottom: 58px;
    color: var(--paper);
    font-size: 20px;
    font-weight: 500;
    letter-spacing: 1px;
  }
</style>
</head>
<body>
<main class="canvas">
  <section class="card card--front">
    <svg class="front-peak" viewBox="0 0 826 471" preserveAspectRatio="none" aria-hidden="true">
      <path d="M257 471 L527 50 Q557 5 587 50 L826 425 L826 471 Z" fill="var(--paper)"/>
    </svg>

    <div class="contact">
      <h1 class="contact__name">Tomas Varenholt</h1>
      <p class="contact__role">Directeur et Fondateur<br>Expert-comptable diplômé</p>
      <p class="contact__address">Rue des Vergières 27<br>1201 Genève</p>
      <ul class="contact__list">
        <li>
          <svg viewBox="0 0 24 24"><path d="M6.6 10.8a15.1 15.1 0 0 0 6.6 6.6l2.2-2.2c.3-.3.7-.4 1-.2 1.1.4 2.3.6 3.6.6.6 0 1 .4 1 1V20c0 .6-.4 1-1 1A17 17 0 0 1 3 4c0-.6.4-1 1-1h3.5c.6 0 1 .4 1 1 0 1.2.2 2.4.6 3.6.1.3 0 .7-.2 1z"/></svg>
          022 418 57 34
        </li>
        <li>
          <svg viewBox="0 0 24 24"><path d="M3 6h18v12H3z" fill="none"/><path d="M3 6l9 6 9-6v12H3z M3 5h18l-9 6z"/></svg>
          tv@clairevalconseil.ch
        </li>
        <li>
          <svg viewBox="0 0 24 24"><circle cx="12" cy="12" r="9"/><path d="M8 7c2 1 2 3 1 4s-2 2 0 4 1 4 1 4M15 5c-1 2 1 3 2 3s2 2 1 4" stroke="var(--navy)" stroke-width="1.6" fill="none"/></svg>
          www.clairevalconseil.ch
        </li>
      </ul>
    </div>

    <p class="brand-name">CLAIREVAL<br>Conseil et Comptes</p>
  </section>

  <section class="card card--back">
    <div class="back-pattern" role="img" aria-label="Motif décoratif répété en bleu clair couvrant tout le verso"></div>
    <p class="back-brand">Claireval</p>
  </section>
</main>
</body>
</html>
```